Building company buisness cards

We are looking for a sharp modern new look for our business cards.We are a New Zealand based company that specialises in house and land packages.We have attached a photo of the current logo and would like to see if it can be improved somehow if needed.We are open to any colours but we have chosen Black and White at this stage. Feel free to change the font and make the logo smarter looking.Play with the colours and see what looks best.We want a card that looks so good know one will want to throw it away!

Target Market(s)

Building profesonals, home buyers

Industry/Entity Type

Building

Contact Information for Business Card

Garrick Tenwood
0275390628
garrickt@hartvale.co.nz

Font styles to use
Serif
Sans Serif

Colors

Designer to choose colors to be used in the design.

Requirements
Must have
• Just the logo on one side and details on the other
• Clean simple looking card
Nice to have
• Round corners and detail like raised or spot UV
• Something that stands out
Should not have
• To title needed, Director etc

```html
<!DOCTYPE html>
<html lang="en">
<head>
<meta charset="utf-8">
<title>Hartvale business cards</title>
<link href="https://fonts.googleapis.com/css2?family=Work+Sans:wght@400;500;600&display=swap" rel="stylesheet">
<style>
  :root {
    --backdrop: #1c1c1d;
    --card: #262627;
    --card-edge: #303031;
    --ink: #f4f4f4;
    --ink-soft: #d6d6d6;
    --spot-uv: #5a5a5c;
  }
  * { margin: 0; padding: 0; box-sizing: border-box; }
  html, body {
    width: 1200px; height: 900px; overflow: hidden;
    background: var(--backdrop);
    font-family: "Work Sans", sans-serif;
  }
  .stage {
    position: relative; width: 1200px; height: 900px;
  }
  .card {
    position: absolute;
    left: 290px;
    width: 620px; height: 354px;
    background: var(--card);
    border: 1px solid var(--card-edge);
    border-radius: 10px;
  }
  .card--front { top: 70px; }
  .card--back { top: 476px; }

  .wordmark {
    display: flex; align-items: center; gap: 14px;
    font-weight: 600; letter-spacing: 0.5px;
  }
  .wordmark__dot {
    border-radius: 50%; border: 2px solid currentColor;
  }
  .card--front .wordmark {
    position: absolute; left: 50%; top: 50%;
    transform: translate(-50%, -50%);
    color: var(--spot-uv); font-size: 56px;
  }
  .card--front .wordmark__dot { width: 58px; height: 58px; }

  .card--back .wordmark {
    position: absolute; left: 46px; top: 150px;
    color: var(--ink); font-size: 40px; gap: 10px;
  }
  .card--back .wordmark__dot { width: 42px; height: 42px; }

  .divider {
    position: absolute; left: 318px; top: 80px;
    width: 2px; height: 200px; background: var(--ink);
  }
  .details {
    position: absolute; left: 350px; top: 96px;
    color: var(--ink);
  }
  .details__name {
    font-size: 21px; font-weight: 500; letter-spacing: 1.5px;
    text-transform: uppercase; margin-bottom: 16px;
  }
  .details__address { font-size: 16px; line-height: 1.3; letter-spacing: 0.6px; margin-bottom: 12px; }
  .contact-list { list-style: none; font-size: 16px; letter-spacing: 0.6px; }
  .contact-list li { display: flex; align-items: center; gap: 10px; line-height: 1.6; }
  .contact-list svg { width: 11px; height: 11px; flex: none; }
</style>
</head>
<body>
<main class="stage">
  <section class="card card--front" aria-label="Card front">
    <div class="wordmark"><span>Hartvale</span><span class="wordmark__dot"></span></div>
  </section>

  <section class="card card--back" aria-label="Card back">
    <div class="wordmark"><span>Hartvale</span><span class="wordmark__dot"></span></div>
    <div class="divider"></div>
    <div class="details">
      <p class="details__name">Garrick Tenwood</p>
      <p class="details__address">218b Marlow Street,<br>Ashbury, NZ, 7042</p>
      <ul class="contact-list">
        <li>
          <svg viewBox="0 0 12 12" fill="none" stroke="currentColor" stroke-width="1.4"><path d="M2 1h2.5l1 3-1.5 1a6 6 0 0 0 3 3l1-1.5 3 1V10a1 1 0 0 1-1 1A9 9 0 0 1 1 2a1 1 0 0 1 1-1z"/></svg>
          0275390628
        </li>
        <li>
          <svg viewBox="0 0 12 12" fill="none" stroke="currentColor" stroke-width="1.2"><rect x="1" y="2.5" width="10" height="7"/><path d="M1 2.5l5 4 5-4"/></svg>
          garrickt@hartvale.co.nz
        </li>
        <li>
          <svg viewBox="0 0 12 12" fill="none" stroke="currentColor" stroke-width="1.1"><circle cx="6" cy="6" r="5"/><ellipse cx="6" cy="6" rx="2.2" ry="5"/><path d="M1 6h10"/></svg>
          www.hartvale.co.nz
        </li>
      </ul>
    </div>
  </section>
</main>
</body>
</html>
```